Modern Business Card

Modern professional business card with more than just logo and demographic info. Something memorable.

We are a trendy/modern chiropractic group with an emphasis on neurology, hence the minimalist-type brain logo. We want to convey that modern and technical aspect with professionalism and the elite nature of our practice environment.

```html
<!DOCTYPE html>
<html lang="en">
<head>
<meta charset="utf-8">
<title>Keystone Spine – Business Card</title>
<link rel="stylesheet" href="https://fonts.googleapis.com/css2?family=Cinzel:wght@400&family=Open+Sans:wght@400&display=swap">
<style>
  :root {
    --bg-top: #d4d3d4;
    --bg-bottom: #f1f1f1;
    --card: #ffffff;
    --brand-blue: #4680c2;
    --ink: #1b1b1b;
    --ink-soft: #3a3a3a;
  }
  * { margin: 0; padding: 0; box-sizing: border-box; }
  html, body { width: 1200px; height: 1200px; overflow: hidden; }
  body {
    background: linear-gradient(180deg, var(--bg-top) 0%, var(--bg-bottom) 100%);
    position: relative;
    font-family: "Open Sans", sans-serif;
  }
  .card {
    position: absolute;
    left: 220px;
    width: 760px;
    height: 434px;
    background: var(--card);
    box-shadow: 0 6px 18px rgba(0,0,0,0.12);
    overflow: hidden;
  }
  .card--front { top: 90px; }
  .card--back { top: 600px; }

  .wordmark {
    display: flex;
    align-items: center;
    gap: 18px;
    font-family: "Cinzel", serif;
    font-weight: 400;
    color: var(--ink);
    letter-spacing: 0.04em;
    line-height: 1;
  }
  .wordmark__dot {
    border-radius: 50%;
    background: var(--brand-blue);
    flex: none;
  }
  .card--front .wordmark {
    position: absolute;
    left: 50%; top: 50%;
    transform: translate(-50%, -50%);
    font-size: 54px;
    white-space: nowrap;
  }
  .card--front .wordmark__dot { width: 58px; height: 58px; }

  .card--back .wordmark {
    position: absolute;
    left: 70px; top: 222px;
    font-size: 34px;
    gap: 12px;
    white-space: nowrap;
  }
  .card--back .wordmark__dot { width: 38px; height: 38px; }

  .contact {
    position: absolute;
    left: 438px; top: 52px;
    color: var(--ink-soft);
  }
  .contact__name {
    font-family: "Cinzel", serif;
    font-size: 27px;
    color: var(--brand-blue);
    letter-spacing: 0.03em;
    line-height: 1.05;
  }
  .contact__role {
    font-size: 13px;
    margin: 2px 0 14px 16px;
    color: var(--ink);
  }
  .contact__row {
    display: flex;
    align-items: center;
    gap: 10px;
    margin-bottom: 10px;
    font-size: 14px;
    line-height: 1.3;
  }
  .contact__row .accent { color: var(--brand-blue); }
  .contact__icon { width: 20px; height: 20px; flex: none; }

  .band {
    position: absolute;
    left: 0; right: 0; bottom: 0;
    height: 66px;
    background: var(--brand-blue);
  }
</style>
</head>
<body>

  <section class="card card--front" aria-label="Card front">
    <div class="wordmark"><span class="wordmark__dot"></span>KEYSTONE SPINE</div>
  </section>

  <section class="card card--back" aria-label="Card back">
    <div class="wordmark"><span class="wordmark__dot"></span>KEYSTONE SPINE</div>

    <div class="contact">
      <p class="contact__name">DANIEL REYES</p>
      <p class="contact__role">Neurologist</p>

      <div class="contact__row">
        <svg class="contact__icon" viewBox="0 0 20 20" aria-hidden="true">
          <circle cx="10" cy="10" r="10" fill="var(--brand-blue)"/>
          <path d="M10 4.5a3.4 3.4 0 0 0-3.4 3.4c0 2.5 3.4 6.4 3.4 6.4s3.4-3.9 3.4-6.4A3.4 3.4 0 0 0 10 4.5z" fill="#fff"/>
          <circle cx="10" cy="8" r="1.3" fill="var(--brand-blue)"/>
        </svg>
        <div>Dummy city<br>Dummy Country Land</div>
      </div>

      <div class="contact__row">
        <svg class="contact__icon" viewBox="0 0 20 20" aria-hidden="true">
          <circle cx="10" cy="10" r="10" fill="var(--brand-blue)"/>
          <path d="M5 9c0-2 2.2-3 5-3s5 1 5 3l-1.8.6-.6-1.6h-5.2l-.6 1.6z" fill="#fff"/>
          <rect x="6.5" y="10" width="7" height="4" rx="1" fill="#fff"/>
          <circle cx="10" cy="12" r="1" fill="var(--brand-blue)"/>
        </svg>
        <div>1-234-567890<br>1-234-567890</div>
      </div>

      <div class="contact__row">
        <svg class="contact__icon" viewBox="0 0 20 20" aria-hidden="true">
          <circle cx="10" cy="10" r="10" fill="var(--brand-blue)"/>
          <circle cx="10" cy="10" r="5" fill="none" stroke="#fff" stroke-width="1.2"/>
          <ellipse cx="10" cy="10" rx="2.2" ry="5" fill="none" stroke="#fff" stroke-width="1"/>
          <line x1="5" y1="10" x2="15" y2="10" stroke="#fff" stroke-width="1"/>
        </svg>
        <div>daniel@<span class="accent">keystonespine</span>.com<br>www.<span class="accent">keystonespine</span>.com</div>
      </div>
    </div>

    <div class="band"></div>
  </section>

</body>
</html>
```